Counseling Practice Business Card

I need a professional looking business card incorporating my new logo that was just completed. Card needs to incorporate my name and title, description of my specialty, my address, my phone number, my fax number, my email and my website URL. I need to be able to choose design on/with different paper colors and textures.
I do not have a lot of business card ideas so I am open to anything but I want bold,sharp, clear card without additional designs other than my logo (see attached file info). I am open to different color backgrounds or paper colors including black. I do not like traditional brackets around area codes in phone number or dashes between numbers in phone number. Am open to other ways of presenting including periods between numbers as appropriate. I do not know enough to know what I like yet but I want card to coordinate and work together with my logo. My practice emphasizes natural mental health interventions so any use of color (with background paper color or the blue and green in my logo) that elicits nature is nice. In addition to black, any natural brown or wood looking background might be desirable also. Most of the offerings so far look very similar and boring.

Target Market(s)

Potential therapy clients and other professionals

Contact Information for Business Card

Card information:
Gerald M. Whitcombe, Ph.D.
Licensed Clinical Psychologist
Integrative Health Coach
4812 Marlowe Ridge Blvd SE
Suite 310
Duluth, GA 30096
(770) 415-2983 phone
(770) 581-4096 fax
drgeraldwhitcombe@quillmarsh.net
brightfernwellness.net

Font styles to use
Serif
Sans Serif
Other font styles liked:
• anything that you think looks crisp, clear and easily readable

Requirements
Must have
• Any color used should coordinate with my logo design (see attached files).
• Card should be printed horizontally so top and bottom are longest sides of rectangle.
• Background color or paper color should complement and highlight logo. Do not like a white background. black, grey, brown or any color my logo would blend well with.
Nice to have
• I would like designer to utilize color to highlight letters/name or phone-fax-web symbols.
• Bottom edge of card could be highlighted if appropriate to an idea.
Should not have
• I would NOT want the card to have a pure white background at all.
• No clear cards.
• Cards should be oriented with long sides on bottom and top, NOT sides. DO NOT LIKE THIS THIN TALL ORIENTATION.

```html
<!DOCTYPE html>
<html lang="en">
<head>
<meta charset="utf-8">
<title>Brightfern Wellness – Business Card</title>
<link rel="stylesheet" href="https://fonts.googleapis.com/css2?family=Source+Sans+3:wght@400;600&display=swap">
<style>
  :root {
    --page: #ffffff;
    --card-center: #232323;
    --card-edge: #121212;
    --brand-blue: #2b74c0;
    --brand-green: #0a6b38;
    --icon-green: #17894a;
    --text-light: #f2f2f2;
  }
  * { box-sizing: border-box; margin: 0; padding: 0; }
  html, body {
    width: 1200px; height: 720px; overflow: hidden;
    background: var(--page);
    font-family: "Source Sans 3", "Helvetica Neue", Arial, sans-serif;
  }
  .canvas { position: relative; width: 1200px; height: 720px; }

  .card {
    position: absolute;
    width: 444px; height: 274px;
    background: radial-gradient(ellipse at 50% 40%, var(--card-center) 0%, var(--card-edge) 100%);
    overflow: hidden;
  }
  .card--front { left: 106px; top: 208px; }
  .card--back  { left: 646px; top: 206px; }

  .edge-band {
    position: absolute; left: 0; right: 0; bottom: 0; height: 10px;
    display: flex;
  }
  .edge-band__green { flex: 1; background: var(--brand-green); }
  .edge-band__blue  { flex: 1; background: var(--brand-blue); }

  .brand-name {
    position: absolute;
    color: var(--brand-blue);
    font-weight: 600;
    white-space: nowrap;
    letter-spacing: 0.5px;
  }
  .card--front .brand-name {
    left: 0; right: 0; top: 108px;
    text-align: center; font-size: 38px;
  }
  .card--back .brand-name {
    left: 18px; top: 124px;
    font-size: 22px;
  }

  .contact { position: absolute; left: 256px; top: 82px; right: 0; }
  .contact__name {
    color: var(--brand-blue); font-size: 12px; font-weight: 400; line-height: 14px;
  }
  .contact__title {
    color: var(--icon-green); font-size: 6.5px; line-height: 9px;
  }
  .contact__rule {
    height: 2px; background: var(--brand-blue); margin-top: 1px;
  }
  .contact__address {
    margin-top: 13px; color: var(--text-light); font-size: 9px; line-height: 12px;
  }
  .contact__lines { list-style: none; margin-top: 11px; }
  .contact__lines + .contact__lines { margin-top: 9px; }
  .contact__line {
    display: flex; align-items: center; gap: 5px;
    color: var(--text-light); font-size: 9px; line-height: 12px;
  }
  .contact__line--bold { font-weight: 600; }
  .icon { width: 9px; height: 9px; flex: none; }
</style>
</head>
<body>
<main class="canvas">

  <section class="card card--front" aria-label="Card front">
    <div class="brand-name">Brightfern Wellness</div>
    <div class="edge-band"><span class="edge-band__green"></span><span class="edge-band__blue"></span></div>
  </section>

  <section class="card card--back" aria-label="Card back">
    <div class="brand-name">Brightfern Wellness</div>

    <div class="contact">
      <p class="contact__name">Gerald M. Whitcombe, Ph.D.</p>
      <p class="contact__title">Licensed Clinical Psychologist / Integrative Health Coach</p>
      <div class="contact__rule"></div>

      <p class="contact__address">4812 Marlowe Ridge Blvd SE Suite 310<br>Duluth, GA 30096</p>

      <ul class="contact__lines">
        <li class="contact__line contact__line--bold">
          <svg class="icon" viewBox="0 0 10 10" aria-hidden="true"><path d="M2 0.8 L3.6 0.8 L4.3 3 L3.2 3.9 Q4.2 6 6.1 6.9 L7 5.8 L9.2 6.5 L9.2 8.1 Q8.9 9.3 7.6 9.2 Q1 8.2 0.8 2.3 Q0.8 0.9 2 0.8 Z" fill="var(--icon-green)"/></svg>
          770 415 2983
        </li>
        <li class="contact__line contact__line--bold">
          <svg class="icon" viewBox="0 0 10 10" aria-hidden="true"><rect x="2.5" y="0.5" width="5" height="3" fill="var(--icon-green)"/><rect x="0.5" y="3.5" width="9" height="4" rx="1" fill="var(--icon-green)"/><rect x="2.5" y="6.5" width="5" height="3" fill="none" stroke="var(--icon-green)"/></svg>
          770 581 4096
        </li>
      </ul>

      <ul class="contact__lines">
        <li class="contact__line">
          <svg class="icon" viewBox="0 0 10 10" aria-hidden="true"><circle cx="5" cy="5" r="4.5" fill="var(--icon-green)"/></svg>
          drgeraldwhitcombe@quillmarsh.net
        </li>
        <li class="contact__line">
          <svg class="icon" viewBox="0 0 10 10" aria-hidden="true"><rect x="0.6" y="1.8" width="8.8" height="6.4" fill="none" stroke="var(--icon-green)" stroke-width="0.9"/><path d="M0.8 2 L5 5.6 L9.2 2" fill="none" stroke="var(--icon-green)" stroke-width="0.9"/></svg>
          brightfernwellness.net
        </li>
      </ul>
    </div>

    <div class="edge-band"><span class="edge-band__green"></span><span class="edge-band__blue"></span></div>
  </section>

</main>
</body>
</html>
```